Nora Flintwick Music EP Design Artwork

EP musical recording cover art work. Nora Flintwick is a new artist in the Pop, Country Pop, Pop Rock, Americana and Singer-songwriter genres. The name of the EP is "Paper Kites at Noon", and her first single is being released on all streaming platforms globally June 1st. We are looking for a graphic design that has that Pop/rock female artist appeal. norafintwick.net and all social media outlets are noraflintwicksongs (reference). Your art work will be seen globally and we will give a personal shout out on all her socials to the design we select as a single post. Her signature logo is attached for a color and style example. Please try to use the signature within the EP cover design, but feel free to change the purple backing accordingly if another color is needed to fit better with the color scheme of your design.

Requirements
Must have
• Nora Flintwick signature logo and EP name

Some of you asked for hi res pics, use this link:

https://files.vantrelbox.net/share/u/0/folders/8KqTz3LmW0pRx7YvN2cJhD5sAa9EgUoiB
Should not have
• June 1 on the EP art work. June 1 is the release of the first single on the EP. This is an album cover, we want it to look like a really cool pop female artist album cover, thanks.

```html
<!DOCTYPE html>
<html lang="en">
<head>
<meta charset="utf-8">
<title>Paper Kites at Noon — Nora Flintwick</title>
<link rel="stylesheet" href="https://fonts.googleapis.com/css2?family=Bebas+Neue&display=swap">
<style>
  :root {
    --stage: #9a9a9a;
    --panel: #ececec;
    --purple: #4a17ad;
    --ink: #111111;
    --brick: #7a4a3c;
    --stone: #d9d9d6;
    --jacket: #1c2230;
    --cream: #dcd0bd;
  }
  * { margin: 0; padding: 0; box-sizing: border-box; }
  html, body {
    width: 1200px;
    height: 900px;
    overflow: hidden;
    background: var(--stage);
  }
  .stage {
    position: relative;
    width: 1200px;
    height: 900px;
    display: flex;
    align-items: center;
    justify-content: center;
  }
  .ep-cover {
    position: relative;
    width: 820px;
    height: 820px;
    background: var(--panel);
    overflow: hidden;
    box-shadow: 0 10px 30px rgba(0, 0, 0, 0.25);
  }
  .artist-photo {
    position: absolute;
    left: 0;
    top: 0;
    width: 370px;
    height: 820px;
    background:
      linear-gradient(90deg, var(--brick) 0%, var(--brick) 8%, rgba(0,0,0,0) 16%),
      linear-gradient(180deg, var(--stone) 0%, #c9c2b9 30%, var(--jacket) 55%, var(--jacket) 72%, var(--cream) 88%, #cfc4b2 100%);
  }
  .ep-title {
    position: absolute;
    left: 402px;
    top: 56px;
    font-family: "Bebas Neue", "Arial Narrow", sans-serif;
    font-size: 172px;
    line-height: 0.82;
    letter-spacing: -1px;
    text-transform: uppercase;
  }
  .ep-title .line { display: block; }
  .ep-title .accent { color: var(--purple); }
  .ep-title .dark { color: var(--ink); }
  .artist-name {
    position: absolute;
    left: 418px;
    top: 676px;
    font-family: "Bebas Neue", "Arial Narrow", sans-serif;
    font-size: 60px;
    line-height: 1;
    color: var(--purple);
  }
</style>
</head>
<body>
  <main class="stage">
    <section class="ep-cover">
      <div class="artist-photo" role="img" aria-label="Portrait of the artist leaning against a pale stone column beside a brick wall, wearing a dark jacket and cream trousers"></div>
      <h1 class="ep-title">
        <span class="line accent">Paper</span>
        <span class="line accent">Kites</span>
        <span class="line dark">At</span>
        <span class="line dark">Noon</span>
      </h1>
      <p class="artist-name">Nora Flintwick</p>
    </section>
  </main>
</body>
</html>
```